New Business Card Design Project

Need a design that will create an impact / strong impression towards our clients for our business. We are in the lighting business and we do lighting retrofits for large commercial to industrial clientele.

Target Market(s)

Lighting Industry

Industry/Entity Type

Business

Font styles to use
Other font styles liked:
• we would like to use the font on our logo, not sure what it is though..

Requirements
Must have
• Our logo.
Nice to have
• We are open to suggestions that have to do with lighting.

```html
<!DOCTYPE html>
<html lang="en">
<head>
<meta charset="utf-8">
<title>Halvorsen Lighting – Business Card</title>
<link rel="stylesheet" href="https://fonts.googleapis.com/css2?family=Roboto+Condensed:wght@400;700&display=swap">
<style>
  :root {
    --page-bg: #ece9e4;
    --card-white: #ffffff;
    --green-dark: #0f4a17;
    --green-mid: #1a8a3f;
    --green-bright: #2fb24c;
    --green-light: #6fcf63;
    --text-muted: #5a5a5a;
    --white: #ffffff;
  }
  * { box-sizing: border-box; margin: 0; padding: 0; }
  html, body { width: 1200px; height: 911px; overflow: hidden; }
  body {
    background: var(--page-bg);
    font-family: "Roboto Condensed", Arial, sans-serif;
    display: flex;
    align-items: center;
    justify-content: center;
    gap: 40px;
  }
  .card {
    width: 520px;
    height: 300px;
    border-radius: 18px;
    position: relative;
    overflow: hidden;
    box-shadow: 0 10px 28px rgba(0,0,0,.18);
  }

  /* Front */
  .card-front { background: var(--card-white); }
  .brand-name {
    position: absolute;
    left: 34px;
    top: 36px;
    font-weight: 700;
    font-size: 26px;
    line-height: 1;
    color: var(--green-dark);
    letter-spacing: .5px;
    text-transform: uppercase;
  }
  .person { position: absolute; right: 34px; top: 30px; text-align: right; }
  .person-name {
    font-weight: 700;
    font-size: 22px;
    color: var(--green-dark);
    letter-spacing: .5px;
  }
  .person-title {
    font-weight: 700;
    font-size: 14px;
    color: var(--green-bright);
    letter-spacing: .5px;
  }
  .contact {
    position: absolute;
    right: 34px;
    top: 104px;
    font-size: 13px;
    line-height: 18px;
    color: var(--text-muted);
    text-align: right;
  }
  .contact-row { display: flex; justify-content: flex-end; align-items: center; gap: 8px; }
  .contact-row svg { width: 11px; height: 11px; fill: var(--green-dark); }
  .contact-gap { height: 8px; }
  .feature-band {
    position: absolute;
    left: 0; bottom: 0;
    width: 300px;
    height: 120px;
    background: linear-gradient(100deg, var(--green-light) 0%, var(--green-mid) 55%, var(--green-dark) 100%);
  }

  /* Back */
  .card-back {
    background: var(--green-dark);
    display: flex;
    align-items: center;
    justify-content: center;
  }
  .back-brand {
    font-weight: 700;
    font-size: 48px;
    line-height: 1;
    color: var(--white);
    letter-spacing: 1px;
    text-transform: uppercase;
  }
  .back-web {
    position: absolute;
    bottom: 24px;
    left: 0; right: 0;
    text-align: center;
    font-size: 12px;
    letter-spacing: 2px;
    color: var(--white);
  }
</style>
</head>
<body>

  <section class="card card-front" aria-label="Card front">
    <div class="brand-name">Halvorsen Lighting</div>

    <div class="person">
      <div class="person-name">DANA WHITFIELD</div>
      <div class="person-title">CEO/FOUNDER</div>
    </div>

    <div class="contact">
      <div>4120 Alder Creek Road</div>
      <div>Fairbanks, Alaska 99701</div>
      <div class="contact-gap"></div>
      <div class="contact-row">907 555 0142
        <svg viewBox="0 0 24 24"><path d="M6.6 10.8a15 15 0 0 0 6.6 6.6l2.2-2.2a1 1 0 0 1 1-.25 11.4 11.4 0 0 0 3.6.57 1 1 0 0 1 1 1V20a1 1 0 0 1-1 1A17 17 0 0 1 3 4a1 1 0 0 1 1-1h3.5a1 1 0 0 1 1 1c0 1.25.2 2.45.57 3.6a1 1 0 0 1-.25 1z"/></svg>
      </div>
      <div class="contact-row">907 555 0187
        <svg viewBox="0 0 24 24"><rect x="3" y="8" width="18" height="12" rx="2"/><rect x="7" y="3" width="10" height="6"/></svg>
      </div>
      <div class="contact-row">907 555 0123
        <svg viewBox="0 0 24 24"><rect x="7" y="2" width="10" height="20" rx="2"/></svg>
      </div>
      <div class="contact-gap"></div>
      <div class="contact-row">dana@halvorsen.com
        <svg viewBox="0 0 24 24"><rect x="2" y="5" width="20" height="14" rx="2"/></svg>
      </div>
      <div class="contact-row">www.halvorsen.com
        <svg viewBox="0 0 24 24"><circle cx="12" cy="12" r="10"/></svg>
      </div>
    </div>

    <div class="feature-band" role="img" aria-label="Decorative green stepped graphic area"></div>
  </section>

  <section class="card card-back" aria-label="Card back">
    <div class="back-brand">Halvorsen Lighting</div>
    <div class="back-web">www.halvorsenlighting.com</div>
  </section>

</body>
</html>
```